Wedding Invitation to be used digitally

Design of a Wedding Invitation.
It will be used digitally by whatsapp, so the file format and image size should be appropriate. We don´t intend to print.
Word file with the text contents as attachment. This is REALLY just the text and the main sequencial order of the information that should appear in the invitation.
However, ALL criativity is welcome ofcourse in terms of organization of the information in the paper, font, uppercase and lowercase, numbers and their format, dates and their format, drawings, logo, etc etc

Target Market(s)

family and friends

Requirements
Must have
• A logo at the top with the capitals of our name - R and T
Nice to have
• Should be elegant

```html
<!DOCTYPE html>
<html lang="en">
<head>
<meta charset="utf-8">
<title>Wedding Invitation – Renata &amp; Tomás</title>
<link rel="stylesheet" href="https://fonts.googleapis.com/css2?family=Quicksand:wght@400;500&family=Nunito:wght@800&display=swap">
<style>
  :root{
    --page:#f3f1f2;
    --marble-dark:#2b2b2e;
    --marble-mid:#46464a;
    --marble-slate:#3a3d47;
    --panel:#282725;
    --gold:#d9a04a;
    --gold-light:#f0c46c;
    --ink:#f4f1ea;
  }
  *{margin:0;padding:0;box-sizing:border-box}
  html,body{width:1200px;height:1200px;overflow:hidden;background:var(--page)}
  .invitation{
    position:absolute;left:298px;top:64px;width:605px;height:1077px;
  }
  .marble{
    position:absolute;inset:0;
    background:
      radial-gradient(ellipse at 20% 10%, var(--marble-mid) 0%, transparent 55%),
      radial-gradient(ellipse at 85% 90%, var(--marble-slate) 0%, transparent 60%),
      linear-gradient(160deg, var(--marble-mid), var(--marble-dark) 45%, var(--marble-slate));
  }
  .panel{
    position:absolute;left:31px;top:96px;width:547px;height:893px;
    background:var(--panel);
    border:2px solid var(--gold);
  }
  .monogram{
    position:absolute;left:50%;top:121px;width:140px;height:140px;
    transform:translate(-50%,-50%);
    border:2px solid var(--gold);border-radius:50%;
    display:flex;align-items:center;justify-content:center;
    font-family:"Quicksand",sans-serif;font-weight:500;font-size:38px;
    color:var(--gold);letter-spacing:1px;
  }
  .line{
    position:absolute;left:0;right:0;text-align:center;
    transform:translateY(-50%);
    font-family:"Quicksand",sans-serif;font-weight:400;
    color:var(--ink);font-size:18px;line-height:1;white-space:nowrap;
  }
  .name{
    font-family:"Nunito",sans-serif;font-weight:800;font-size:27px;
    background:linear-gradient(90deg,var(--gold-light),var(--gold));
    -webkit-background-clip:text;background-clip:text;color:transparent;
  }
  .ampersand{font-size:24px;color:var(--gold)}
  .dots{color:var(--gold);font-size:14px;letter-spacing:7px;padding-left:7px}
</style>
</head>
<body>
  <main class="invitation">
    <div class="marble" role="img" aria-label="Dark grey marble texture with gold veins"></div>
    <section class="panel">
      <div class="monogram">R&amp;T</div>
      <p class="line" style="top:277px">Together with their families</p>
      <p class="line name" style="top:323px">Renata Alves</p>
      <p class="line ampersand" style="top:368px">&amp;</p>
      <p class="line name" style="top:410px">Tomás Navarro</p>
      <p class="line" style="top:458px">Invite you to their Wedding Celebration</p>
      <p class="line dots" style="top:487px">••••••••••</p>
      <p class="line" style="top:517px">Sunday, July 28, 2024</p>
      <p class="line" style="top:550px">At 11H30</p>
      <p class="line dots" style="top:579px">••••••••••</p>
      <p class="line" style="top:609px">Capela de Santa Luzia | Vale Claro</p>
      <p class="line" style="top:644px">(Parking – Marina do Vale or Parque Terra Norte)</p>
      <p class="line dots" style="top:670px">••••••••••</p>
      <p class="line" style="top:698px">Reception to Follow</p>
      <p class="line" style="top:729px">At</p>
      <p class="line" style="top:762px">Hotel Brisa Lunar do Rochedo | Vale Claro</p>
      <p class="line" style="top:796px">(Parking – on site)</p>
      <p class="line dots" style="top:824px">••••••••••</p>
      <p class="line" style="top:854px">RSVP by 20th July</p>
    </section>
  </main>
</body>
</html>
```